2 page Web Site Design (Coded), simple, not picky

I need a web portal for a PPC marketing business. I have the logo, some imagery, and some websites to base the design on.

***Background***
The name of the business is "Quiet Harbor Outreach Partners" or QHOP. We provide listings in a searchable database for Dental Sleep Medicine doctors. These are doctors who treat snoring/sleep apnea/and CPAP users with oral appliances. Client doctors will have their own "landing page website" where PPC prospects land from the PPC campaigns. Logos for supporting/landing page websites have been uploaded.
***End Background***

THIS website (for you to design) is to introduce doctors to the concept and detail the services. i.e. PPC campaign management services, listing on a national database of Dental Sleep Medicine practitioners, and a fully featured website dedicated to Snoring, Sleep Apnea, and CPAP Alternative treatment (those websites are "Farewell-Rumble.com", "Farewell-NightGasp.com", and ""Farewell-MaskTube.com")

SEM websites whose look I enjoy are:

http://www.brightlorn.example/marketing-services/pay-per-click/

http://www.parcelwindow.example/welcome/pay-per-click-services/

http://www.tessaroqco.example/marketing-services/paid-search-management/

The main colors are Red, White, & Blue. Red and blue used mostly for accents/emphasis.

The main/index page's purpose is to, as best possible, convey the idea of SEM campaign management with supporting websites being their best option for internet marketing!
The secondary page is just a slightly modified layout where details can be explained.

Target Market(s)

Dentists who practice Dental Sleep Medicine (see www.ovrqx.example)

Industry/Entity Type

Marketing

Requirements
Must have
• -Sign-up form for the generation of leads... Simple script that sends E-mail is fine... Doctor's Name, Business Name, Business Address, E-mail address, phone #.

-Graphics that will clearly describe the services being provided.

```html
<!DOCTYPE html>
<html lang="en">
<head>
<meta charset="utf-8">
<title>Quiet Harbor Outreach Partners</title>
<link rel="stylesheet" href="https://fonts.googleapis.com/css2?family=Arimo:wght@400;700&family=Roboto+Condensed:wght@400;700&display=swap">
<style>
  :root {
    --red: #b3242d;
    --red-dark: #8f1a22;
    --blue: #1a3a7e;
    --blue-dark: #122c66;
    --link-blue: #1f4f9a;
    --text: #333333;
    --muted: #555555;
    --page-bg: #ebebeb;
    --white: #ffffff;
    --field: #e2e2e2;
    --line: #d8d8d8;
  }
  * { box-sizing: border-box; margin: 0; padding: 0; }
  html, body { width: 1063px; height: 1200px; overflow: hidden; background: var(--page-bg); }
  body { font-family: "Arimo", Arial, sans-serif; color: var(--text); }
  .page { position: relative; width: 1198px; height: 1353px; transform: scale(0.8873); transform-origin: 0 0; background: var(--page-bg); }
  .abs { position: absolute; }

  /* header */
  .site-header { left: 0; top: 0; width: 1198px; height: 90px; background: linear-gradient(#ffffff, #f1f1f1); }
  .brand { left: 130px; top: 22px; display: flex; align-items: center; gap: 10px; }
  .brand-dot { width: 40px; height: 40px; border-radius: 50%; background: var(--blue); }
  .brand-name { font-family: "Arimo", Arial, sans-serif; font-weight: 700; font-size: 38px; color: var(--red); letter-spacing: 1px; }
  .main-nav { left: 586px; top: 32px; display: flex; align-items: center; font-size: 14px; }
  .main-nav a { color: var(--link-blue); text-decoration: none; }
  .main-nav .current { background: linear-gradient(#3d6fc4, #1c4596); color: var(--white); border: 2px solid #163a82; border-radius: 14px; padding: 4px 11px; margin-right: 73px; }
  .main-nav .item { margin-right: 86px; }
  .main-nav .item:last-child { margin-right: 0; }

  /* hero */
  .hero { left: 0; top: 90px; width: 1198px; height: 431px; background: linear-gradient(100deg, #6d6a68 0%, #a39f9c 25%, #5a4e4a 50%, #8d7c76 72%, #5e3e37 100%); }
  .hero-title { left: 131px; top: 140px; font-family: "Roboto Condensed", Arial, sans-serif; font-weight: 700; font-size: 23px; color: var(--white); text-shadow: 1px 1px 2px rgba(0,0,0,.6); }
  .promise-panel { left: 447px; top: 224px; width: 616px; height: 276px; background: rgba(255,255,255,.72); border: 1px solid rgba(255,255,255,.9); border-radius: 4px; padding: 32px 36px 0 36px; }
  .promise-panel h2 { font-weight: 400; font-size: 17px; line-height: 22px; color: var(--link-blue); margin-bottom: 18px; }
  .promise-list { list-style: none; }
  .promise-list li { position: relative; padding-left: 26px; font-size: 13px; line-height: 17px; color: #222; margin-bottom: 19px; }
  .promise-list svg { position: absolute; left: 4px; top: 4px; }

  /* cards */
  .card-red { left: 136px; top: 207px; width: 309px; height: 353px; background: var(--red); border: 1px solid #d2555c; color: var(--white); }
  .card-blue { left: 136px; top: 629px; width: 309px; height: 292px; background: var(--blue); border-radius: 3px; color: var(--white); }
  .card-head { text-align: center; padding-top: 14px; height: 74px; border-bottom: 1px solid rgba(255,255,255,.18); }
  .card-head h2 { font-family: "Roboto Condensed", Arial, sans-serif; font-weight: 400; font-size: 24px; line-height: 28px; }
  .card-head p { font-size: 13px; margin-top: 1px; }
  .card-red .intro { font-size: 12px; line-height: 14.5px; padding: 12px 20px 0 14px; }
  .card-list { list-style: none; padding: 16px 20px 0 14px; }
  .card-list li { position: relative; padding-left: 30px; font-size: 12px; line-height: 14px; margin-bottom: 13px; }
  .card-list li::before { content: ""; position: absolute; left: 13px; top: 5px; border-left: 4px solid var(--white); border-top: 2.5px solid transparent; border-bottom: 2.5px solid transparent; }
  .card-blue .card-list { padding-top: 14px; }
  .card-blue .card-list li { font-size: 11px; line-height: 13px; margin-bottom: 14px; }
  .btn-more { left: 192px; top: 311px; width: 100px; height: 26px; border-radius: 13px; background: linear-gradient(#4d7fd2, #1d4aa0); border: 1px solid #16397e; color: var(--white); font-size: 14px; text-align: center; line-height: 24px; }
  .soft-shadow { height: 12px; border-radius: 50%; background: radial-gradient(ellipse at center, rgba(0,0,0,.22), rgba(0,0,0,0) 70%); }

  /* content */
  .content-box { left: 120px; top: 546px; width: 958px; height: 743px; background: var(--white); border: 1px solid var(--line); border-radius: 4px; }
  .article { left: 473px; top: 577px; width: 578px; }
  .article h1 { font-family: "Roboto Condensed", Arial, sans-serif; font-weight: 400; font-size: 23px; color: #222; padding: 0 0 8px 2px; border-bottom: 1px solid var(--line); margin-bottom: 12px; }
  .article h3 { font-size: 17px; font-weight: 700; color: var(--link-blue); margin: 0 0 18px; }
  .article p { font-size: 12px; line-height: 18px; color: var(--muted); }
  .lead { margin-bottom: 22px; }
  .results-figure { width: 580px; height: 258px; margin: 18px 0 26px -1px; border: 1px solid var(--line); display: flex; gap: 14px; padding: 4px; }
  .results-figure div { flex: 1; background: linear-gradient(#f2f0dc, #faf8ea 40%, #ffffff); border: 1px solid #cfcfcf; }
  .article ul { list-style: none; margin-top: 18px; }
  .article ul li { position: relative; padding-left: 13px; font-size: 12px; line-height: 18px; color: var(--muted); }
  .article ul li::before { content: ""; position: absolute; left: 0; top: 6px; border-left: 4px solid var(--red); border-top: 2.5px solid transparent; border-bottom: 2.5px solid transparent; }
  .read-more { display: inline-block; margin-top: 6px; font-size: 11px; font-weight: 700; color: var(--link-blue); text-decoration: none; }

  /* signup */
  .signup { left: 136px; top: 946px; width: 309px; height: 323px; background: var(--white); border: 1px solid var(--line); border-radius: 3px; }
  .signup h2 { font-family: "Roboto Condensed", Arial, sans-serif; font-weight: 400; font-size: 23px; color: #222; text-align: center; height: 62px; padding-top: 15px; border-bottom: 1px solid var(--line); background: linear-gradient(#ffffff, #f4f4f4); }
  .field { position: absolute; left: 20px; font-size: 12px; color: #333; }
  .field-input { position: absolute; left: 140px; width: 151px; height: 22px; border: 1px solid #c6c6c6; border-radius: 4px; background: linear-gradient(#f2f2f2, var(--field)); }
  .btn-submit { left: 140px; top: 279px; width: 93px; height: 27px; border-radius: 14px; background: linear-gradient(#d0343d, var(--red-dark)); border: 1px solid #7a141b; color: var(--white); font-size: 14px; text-align: center; line-height: 25px; }

  .site-footer { left: 122px; top: 1308px; font-size: 10px; line-height: 12px; color: #555; }
</style>
</head>
<body>
<div class="page">
  <header class="site-header abs">
    <div class="brand abs"><span class="brand-dot"></span><span class="brand-name">QHOP</span></div>
    <nav class="main-nav abs">
      <a class="current" href="#">Landing Page</a>
      <a class="item" href="#">About</a>
      <a class="item" href="#">Services</a>
      <a class="item" href="#">Contact</a>
    </nav>
  </header>

  <section class="hero abs" role="img" aria-label="Photo of a doctor reviewing rising growth charts"></section>
  <div class="hero-title abs">Quiet Harbor Outreach Partners</div>

  <div class="promise-panel abs">
    <h2>Each participant has a customized “landing page” on a website that exclusively promotes the OSB therapies and OSB therapists.</h2>
    <ul class="promise-list">
      <li><svg width="8" height="8" viewBox="0 0 8 8"><path d="M7 1 L1 7 M1 2 V7 H6" stroke="#b3242d" stroke-width="1.6" fill="none"/></svg>We set up and manage your search engine marketing campaigns for you.</li>
      <li><svg width="8" height="8" viewBox="0 0 8 8"><path d="M7 1 L1 7 M1 2 V7 H6" stroke="#b3242d" stroke-width="1.6" fill="none"/></svg>You only pay when visitors click on your ad and visit your website.</li>
      <li><svg width="8" height="8" viewBox="0 0 8 8"><path d="M7 1 L1 7 M1 2 V7 H6" stroke="#b3242d" stroke-width="1.6" fill="none"/></svg>We design your ad campaign to optimize ad click conversion rates.</li>
      <li><svg width="8" height="8" viewBox="0 0 8 8"><path d="M7 1 L1 7 M1 2 V7 H6" stroke="#b3242d" stroke-width="1.6" fill="none"/></svg>We send you regular advertising effectiveness monitoring, and analysis reports so you can determine your return-on-investment and adjust your budget accordingly.</li>
    </ul>
  </div>

  <div class="content-box abs"></div>

  <section class="card-red abs">
    <div class="card-head"><h2>Search Engine Marketing</h2><p>Online marketing strategy</p></div>
    <p class="intro">Search engine marketing is an online marketing strategy that aims to increase qualified visitor traffic to your website by positioning your advertisements at the top and right side of “natural” and “organic” search result pages</p>
    <ul class="card-list">
      <li>You only pay when someone clicks on one of your advertisements.</li>
      <li>It is estimated that pay per click ads receive around 30% of all clicks on search engines.</li>
      <li>Seekwell AdPlace, Hollerhub Search Marketing and Tandem AdCentral are pay per click advertising platforms.</li>
    </ul>
    <div class="btn-more abs">More</div>
  </section>
  <div class="soft-shadow abs" style="left:166px;top:566px;width:250px;"></div>

  <section class="card-blue abs">
    <div class="card-head" style="height:77px;padding-top:15px;"><h2>Pay Per Click</h2><p style="font-size:12px;margin-top:3px;">Search Engine Marketing Campaign Managment.</p></div>
    <ul class="card-list">
      <li>We set up and manage your search engine marketing campaigns for you.</li>
      <li>You only pay when visitors click on your ad and visit your website.</li>
      <li>We design your ad campaign to optimize ad click conversion rates.</li>
      <li>We send you regular advertising effectiveness monitoring, and analysis reports so you can determine your return-on-investment and adjust your budget accordingly.</li>
    </ul>
  </section>
  <div class="soft-shadow abs" style="left:166px;top:918px;width:250px;height:8px;"></div>

  <form class="signup abs">
    <h2>Signup Today!</h2>
    <label class="field" style="top:82px;">Doctor's Name</label><span class="field-input" style="top:78px;"></span>
    <label class="field" style="top:113px;">Business Name</label><span class="field-input" style="top:108px;"></span>
    <label class="field" style="top:144px;">Business Address</label><span class="field-input" style="top:139px;height:64px;"></span>
    <label class="field" style="top:215px;left:23px;">E-mail address</label><span class="field-input" style="top:212px;"></span>
    <label class="field" style="top:246px;">Phone.No</label><span class="field-input" style="top:243px;"></span>
    <div class="btn-submit abs">Submit</div>
  </form>
  <div class="soft-shadow abs" style="left:166px;top:1265px;width:250px;height:8px;"></div>

  <main class="article abs">
    <h1>Welcome to Quiet Harbor Outreach Partners</h1>
    <p class="lead">will drive customers to your practice with PPC Search engine Marketing and then educate them about the unique benefits inherent to OAT therapy with a dedicated website .</p>
    <h3>What is Search Engine Marketing?</h3>
    <p>Search engine marketing is an online marketing strategy that aims to increase qualified visitor traffic to your website by positioning your advertisements at the top and right side of “natural” and “organic” search result pages [descriptions below].</p>
    <div class="results-figure" role="img" aria-label="Two search result pages highlighting pay per click ads and natural search results">
      <div></div><div></div>
    </div>
    <h3>Search Engine Marketing(Pay Per Click)</h3>
    <p>Paid search results, called “Pay Per Click” (PPC) advertising, promote websites in “Sponsored” section of search results.</p>
    <ul>
      <li>You only pay when someone clicks on one of your advertisements.</li>
      <li>It is estimated that pay per click ads receive around 30% of all clicks on search engines.</li>
      <li>Seekwell AdPlace, Hollerhub Search Marketing and Tandem AdCentral are pay per click advertising platforms.</li>
    </ul>
    <a class="read-more" href="#">Read More...</a>
  </main>

  <footer class="site-footer abs">Copyrights@Quiet Harbor Outreach Partners.com<br>All rights reserved.</footer>
</div>
</body>
</html>
```